Software Development Consulting Company Needs Business Card Design

We need a new business card design for our consultants at Kestrel Works (kestrelworks.example). We are a small firm that provides high-end software development and methodology consulting to medium to large enterprise IT organizations.

Our logo uses Futura for the font and we would like to stick with navy blue and canary yellow for the logo colors. Attached are normal and reversed versions of our logos in illustrator format.
Updates

Hi Everyone, Thank yo very much for your amazing design ideas. I have created a poll for this project and our employees will be voting on the design they wish to use. We will be making a decision this Wednesday (October 22nd). Thanks again, Dale Hartwick

Industry/Entity Type

Business

```html
<!DOCTYPE html>
<html lang="en">
<head>
<meta charset="utf-8">
<title>Kestrel Works — Business Card</title>
<link rel="stylesheet" href="https://fonts.googleapis.com/css2?family=Jost:wght@400;500;700&display=swap">
<style>
  :root {
    --navy: #1f4672;
    --canary: #f7e91b;
    --paper: #ffffff;
    --backdrop: #e9e6e1;
    --ink-soft: #3a4a5e;
  }
  * { box-sizing: border-box; margin: 0; padding: 0; }
  html, body {
    width: 1200px; height: 720px; overflow: hidden;
    background: var(--backdrop);
    font-family: "Jost", "Futura", sans-serif;
  }
  .sheet {
    width: 1200px; height: 720px;
    display: flex; align-items: center; justify-content: center; gap: 40px;
  }
  .card {
    position: relative;
    width: 540px; height: 309px;
    background: var(--paper);
    overflow: hidden;
    box-shadow: 0 6px 18px rgba(0,0,0,0.14);
  }
  .card-front .swoosh { position: absolute; inset: 0; width: 100%; height: 100%; }

  .brand {
    position: absolute; display: flex; align-items: center; gap: 10px;
    color: var(--navy); font-weight: 500; letter-spacing: 0.14em; text-transform: uppercase;
    white-space: nowrap;
  }
  .brand-dot { border-radius: 50%; background: var(--canary); flex: none; }
  .card-front .brand { top: 38px; left: 34px; font-size: 30px; }
  .card-front .brand-dot { width: 16px; height: 16px; }

  .holder { position: absolute; left: 40px; top: 148px; color: var(--navy); }
  .holder-name { font-size: 17px; font-weight: 700; }
  .holder-title { font-size: 14px; font-weight: 400; color: var(--ink-soft); }
  .holder-place {
    margin-top: 10px; display: flex; align-items: center; gap: 6px;
    font-size: 12.5px; color: var(--ink-soft);
  }
  .holder-place svg { width: 11px; height: 14px; fill: var(--navy); }

  .contact {
    position: absolute; right: 24px; top: 150px;
    list-style: none; color: var(--paper); font-size: 13px;
    display: flex; flex-direction: column; align-items: flex-end; gap: 8px;
    white-space: nowrap;
  }
  .contact li { display: flex; align-items: center; gap: 7px; }
  .contact svg { width: 12px; height: 12px; fill: none; stroke: var(--paper); stroke-width: 1.6; }

  .card-back .brand {
    top: 112px; left: 0; right: 0; justify-content: center; font-size: 34px;
  }
  .card-back .brand-dot { width: 18px; height: 18px; }
  .back-domain {
    position: absolute; right: 44px; top: 168px;
    color: var(--navy); font-size: 13px; letter-spacing: 0.12em;
  }
  .back-url {
    position: absolute; left: 0; right: 0; bottom: 38px; text-align: center;
    color: var(--navy); font-size: 17px; letter-spacing: 0.16em;
  }
  .back-url strong { font-weight: 700; }
</style>
</head>
<body>
<main class="sheet">
  <section class="card card-front" aria-label="Business card front">
    <svg class="swoosh" viewBox="0 0 540 309" preserveAspectRatio="none" aria-hidden="true">
      <path d="M0,309 L0,300 C150,296 240,270 300,200 C350,140 420,115 540,108 L540,309 Z" fill="var(--navy)"/>
      <path d="M0,286 C150,282 236,256 293,188 C343,127 420,101 540,94" fill="none" stroke="var(--canary)" stroke-width="9"/>
      <path d="M0,272 C150,268 232,242 286,175 C336,114 420,88 540,80" fill="none" stroke="var(--canary)" stroke-width="3"/>
    </svg>

    <div class="brand">
      <span class="brand-dot"></span>
      <span class="brand-name">Kestrel Works</span>
    </div>

    <div class="holder">
      <p><span class="holder-name">Your Name,</span> <span class="holder-title">Title</span></p>
      <p class="holder-place">
        <svg viewBox="0 0 10 14"><path d="M5 0a5 5 0 0 0-5 5c0 3.6 5 9 5 9s5-5.4 5-9a5 5 0 0 0-5-5zm0 7a2 2 0 1 1 0-4 2 2 0 0 1 0 4z"/></svg>
        Lakeport + Fairview, IL
      </p>
    </div>

    <ul class="contact">
      <li>
        <svg viewBox="0 0 12 12"><path d="M2.5 1h2l1 3-1.5 1a6 6 0 0 0 3 3l1-1.5 3 1v2a1 1 0 0 1-1 1A10 10 0 0 1 1.5 2a1 1 0 0 1 1-1z"/></svg>
        012-555-0147
      </li>
      <li>
        <svg viewBox="0 0 12 12"><rect x="1" y="2.5" width="10" height="7" rx="1"/><path d="M1 3l5 4 5-4"/></svg>
        info@kestrelworks.example
      </li>
      <li>
        <svg viewBox="0 0 12 12"><circle cx="6" cy="6" r="5"/><path d="M1 6h10M6 1c2.5 3 2.5 7 0 10M6 1c-2.5 3-2.5 7 0 10"/></svg>
        www.kestrelworks.example
      </li>
    </ul>
  </section>

  <section class="card card-back" aria-label="Business card back">
    <div class="brand">
      <span class="brand-dot"></span>
      <span class="brand-name">Kestrel Works</span>
    </div>
    <p class="back-domain">kestrelworks.example</p>
    <p class="back-url">www.<strong>kestrelworks</strong>.example</p>
  </section>
</main>
</body>
</html>
```